Non fiction leadership Book Cover design needed for “Stay Bold: Build On Lasting Discipline”

I need a front cover design for a new book 6 X 9 traditional non-fiction book.

Title: "Stay BOLD - Build On Lasting Discipline"

The subtitle is not finalized- so use 2 lines of smaller dummy text

My brand guide is attached (please use the tan color sparingly)

I'd like to see BOLD look like it is in motion and "flying" across the page

Need CREATIVE designs and options

Do not want my picture on the front cover - I do want it on the back cover.

On the front cover I’d like to see creative use of font to create movement on “BOLD”

Target Market(s)

Business leaders

Industry/Entity Type

Aviation

Font styles to use
Other font styles liked:
• See style guide- can add additional font (modern script or san serif)

Colors
0054AA
0677BA
7BADD7
CADEEF
E8F1F8
EB3D1F
EC4F4E
F09395
F8D3D4
FCEDEE

Requirements
Must have
• Creative font use, using perspective to create movement/motion on BOLD
Should not have
• My picture on the front cover- my picture should be on the back cover

```html
<!DOCTYPE html>
<html lang="en">
<head>
<meta charset="UTF-8">
<title>Stay Bold: Build On Lasting Discipline — Book Cover</title>
<link rel="stylesheet" href="https://fonts.googleapis.com/css2?family=Archivo+Black&family=Roboto:wght@900&family=Roboto+Condensed:wght@700&family=Montserrat:wght@700&family=Nunito+Sans:wght@400&display=swap">
<style>
  :root {
    --paper-light: #fbfaf3;
    --paper-shade: #eeeeee;
    --signal-red: #c0202b;
    --ink-navy: #14192e;
    --deep-blue: #0054aa;
    --sky-blue: #0677ba;
    --slate: #3a3f4a;
    --bronze-dark: #9a5a28;
    --bronze-mid: #c48a52;
    --bronze-light: #ebbf8a;
  }
  * { margin: 0; padding: 0; box-sizing: border-box; }
  html, body { width: 800px; height: 1200px; overflow: hidden; }
  body { background: var(--paper-shade); }

  .cover {
    position: relative;
    width: 800px;
    height: 1200px;
    overflow: hidden;
    background: linear-gradient(200deg, var(--paper-light) 0%, #f6f5ef 50%, var(--paper-shade) 100%);
  }

  .hero-artwork {
    position: absolute;
    left: 0; top: 40px;
    width: 760px; height: 400px;
    background: linear-gradient(160deg, rgba(20,25,46,0.55) 0%, rgba(58,63,74,0.35) 40%, rgba(196,138,82,0.25) 70%, rgba(251,250,243,0) 100%);
    clip-path: polygon(0 30%, 100% 0, 100% 40%, 0 100%);
  }

  .title-stay {
    position: absolute;
    top: 424px; left: 257px;
    font-family: "Archivo Black", sans-serif;
    font-size: 92px;
    line-height: 1;
    color: var(--signal-red);
    letter-spacing: 1px;
  }

  .motion-lines {
    position: absolute;
    top: 520px; left: 0;
    width: 200px; height: 180px;
  }

  .title-bold-stage {
    position: absolute;
    top: 492px; left: 150px;
    width: 620px; height: 230px;
    perspective: 700px;
  }
  .title-bold {
    display: inline-block;
    font-family: "Roboto", sans-serif;
    font-weight: 900;
    font-size: 236px;
    line-height: 1;
    letter-spacing: -6px;
    transform-origin: left center;
    transform: rotateY(24deg) skewX(-12deg);
    background: linear-gradient(90deg, var(--ink-navy) 0%, var(--deep-blue) 55%, var(--sky-blue) 100%);
    -webkit-background-clip: text;
    background-clip: text;
    color: transparent;
  }

  .title-expansion {
    position: absolute;
    top: 722px; left: 164px;
    font-family: "Roboto Condensed", sans-serif;
    font-weight: 700;
    font-size: 38px;
    line-height: 1;
    color: var(--ink-navy);
  }

  .subtitle {
    position: absolute;
    top: 832px; left: 0; width: 100%;
    text-align: center;
    font-family: "Roboto Condensed", sans-serif;
    font-weight: 700;
    font-size: 56px;
    line-height: 1;
    color: var(--signal-red);
  }

  .secondary-title {
    position: absolute;
    top: 914px; left: 0; width: 100%;
    text-align: center;
    font-family: "Montserrat", sans-serif;
    font-weight: 700;
    font-size: 21px;
    color: var(--ink-navy);
  }

  .body-copy {
    position: absolute;
    top: 958px; left: 0; width: 100%;
    text-align: center;
    font-family: "Nunito Sans", sans-serif;
    font-size: 20px;
    line-height: 28px;
    color: var(--ink-navy);
  }

  .author-band {
    position: absolute;
    top: 1090px; left: 0;
    width: 800px; height: 46px;
  }
  .author-band .bar {
    position: absolute;
    top: 0; height: 46px;
    background: linear-gradient(90deg, var(--bronze-dark), var(--bronze-light));
  }
  .author-band .bar-left { left: 0; width: 42px; }
  .author-band .bar-right { left: 608px; width: 192px; }
  .author-name {
    position: absolute;
    left: 68px; top: 0;
    line-height: 46px;
    font-family: "Montserrat", sans-serif;
    font-weight: 700;
    font-size: 35px;
    letter-spacing: 7px;
    color: var(--ink-navy);
  }
</style>
</head>
<body>
  <main class="cover">
    <div class="hero-artwork" role="img" aria-label="Slate and bronze arrows surging upward alongside a formation of helicopter silhouettes in flight"></div>

    <h1 class="book-title">
      <span class="title-stay">STAY</span>
      <svg class="motion-lines" viewBox="0 0 200 180" aria-hidden="true">
        <line x1="20" y1="30" x2="190" y2="30" stroke="#0054aa" stroke-width="6" stroke-linecap="round" opacity="0.35"/>
        <line x1="60" y1="62" x2="195" y2="62" stroke="#14192e" stroke-width="8" stroke-linecap="round" opacity="0.5"/>
        <line x1="0" y1="96" x2="185" y2="96" stroke="#0677ba" stroke-width="5" stroke-linecap="round" opacity="0.3"/>
        <line x1="40" y1="128" x2="192" y2="128" stroke="#14192e" stroke-width="7" stroke-linecap="round" opacity="0.45"/>
        <line x1="90" y1="158" x2="188" y2="158" stroke="#0054aa" stroke-width="4" stroke-linecap="round" opacity="0.3"/>
      </svg>
      <span class="title-bold-stage"><span class="title-bold">BOLD</span></span>
      <span class="title-expansion">BUILD ON LASTING DISCIPLINE</span>
    </h1>

    <p class="subtitle">SUBTITLE PLACEHOLDER</p>
    <p class="secondary-title">Smaller Secondary Title Placeholder</p>
    <p class="body-copy">Nunito Sans Font Family for All Body Copy -<br>Lorem ipsum dolor sit amet, consectetur adipiscing elit.</p>

    <div class="author-band">
      <span class="bar bar-left"></span>
      <span class="author-name">Margaret Ellison</span>
      <span class="bar bar-right"></span>
    </div>
  </main>
</body>
</html>
```